Chimney Service company needs new business card design

We need a updated business card with our new logo added. We provide a full range of chimney services throughout Vermont and New Hampshire. The business card will be one sided and color. Attached is our current business card another document showing all the information we would like on the card.
We dont like a lot of flashy colors.... here is a link to our website to get an idea of our branding www.flueguardianvt.example

Target Market(s)

homeowners

Industry/Entity Type

Business

Contact Information for Business Card

See attached sheet for content.

Font styles to use
Serif
Sans Serif

Requirements
Must have
• all information provided on separate sheet
Should not have
• Additional information that may clogg up design

```html
<!DOCTYPE html>
<html lang="en">
<head>
<meta charset="utf-8">
<title>Flue Guardian – Business Card</title>
<link href="https://fonts.googleapis.com/css2?family=Marcellus&family=Raleway:wght@400&display=swap" rel="stylesheet">
<style>
  :root {
    --page: #e9e6e1;
    --card-dark: #2b2b2d;
    --card-mid: #3d3d40;
    --ink: #f2f2f2;
    --ink-soft: #d9d9d9;
    --accent: #b3222a;
    --ember: #5a2a30;
  }
  html, body {
    margin: 0;
    width: 1200px;
    height: 1022px;
    overflow: hidden;
    background: var(--page);
  }
  .card {
    position: absolute;
    left: 100px;
    top: 225px;
    width: 1000px;
    height: 571px;
    border-radius: 6px;
    background: linear-gradient(160deg, var(--card-mid) 0%, var(--card-dark) 60%, #242426 100%);
    box-shadow: 0 10px 30px rgba(0,0,0,.25);
    overflow: hidden;
    font-family: "Marcellus", serif;
    color: var(--ink);
  }
  .ember-glow {
    position: absolute;
    right: -60px;
    top: -40px;
    width: 560px;
    height: 520px;
    border-radius: 50%;
    background: radial-gradient(ellipse at 55% 40%, rgba(90,42,48,.9) 0%, rgba(90,42,48,.45) 45%, rgba(90,42,48,0) 72%);
  }
  .brand-square {
    position: absolute;
    left: 70px;
    top: 60px;
    width: 110px;
    height: 110px;
    border: 7px solid var(--ink);
    box-sizing: border-box;
  }
  .brand-name {
    position: absolute;
    left: 60px;
    top: 205px;
    margin: 0;
    font-size: 44px;
    font-weight: 400;
    letter-spacing: 3px;
    white-space: nowrap;
  }
  .brand-rule {
    position: absolute;
    left: 60px;
    top: 268px;
    width: 370px;
    display: flex;
    align-items: center;
    gap: 10px;
    font-size: 14px;
    letter-spacing: 3px;
    color: var(--ink-soft);
  }
  .brand-rule::before, .brand-rule::after {
    content: "";
    flex: 1;
    height: 2px;
    background: var(--ink);
  }
  .accent-line {
    position: absolute;
    left: 60px;
    top: 300px;
    width: 560px;
    height: 2px;
    background: var(--accent);
  }
  .services {
    position: absolute;
    left: 60px;
    top: 322px;
    margin: 0;
    padding: 0;
    list-style: none;
    font-size: 24px;
    line-height: 34px;
    letter-spacing: 1px;
  }
  .services li::before {
    content: "";
    display: inline-block;
    width: 9px;
    height: 9px;
    border-radius: 50%;
    background: var(--ink);
    margin: 0 14px 4px 0;
    vertical-align: middle;
  }
  .contact {
    position: absolute;
    right: 60px;
    top: 50px;
    margin: 0;
    padding: 0;
    list-style: none;
    text-align: right;
    font-family: "Raleway", sans-serif;
    font-size: 24px;
    line-height: 38px;
    color: var(--ink);
  }
  .contact li { display: flex; align-items: center; justify-content: flex-end; gap: 14px; }
  .contact svg { width: 22px; height: 22px; flex: none; }
  .base-line {
    position: absolute;
    left: 0;
    right: 0;
    bottom: 40px;
    height: 2px;
    background: var(--ink-soft);
  }
</style>
</head>
<body>
  <main class="card">
    <div class="ember-glow" role="img" aria-label="Large soft ember-toned decorative area"></div>

    <div class="brand-square"></div>
    <h1 class="brand-name">FLUE GUARDIAN</h1>
    <div class="brand-rule">INC 1994</div>
    <div class="accent-line"></div>

    <ul class="services">
      <li>FULL MASONRY SERVICES</li>
      <li>HISTORIC CHIMNEY RESTORATION</li>
      <li>STAINLESS STEEL LINERS</li>
      <li>STATE CERTIFIED CHIMNEY SWEEP</li>
      <li>FULLY INSURED &bull; FREE ESTIMATES</li>
    </ul>

    <ul class="contact">
      <li>802-555-0142
        <svg viewBox="0 0 22 22" aria-hidden="true"><circle cx="11" cy="11" r="11" fill="#b3222a"/><path d="M7.5 6c1 0 1.3 2 1.3 2.4s-.8.9-.8 1.2c.4 1.3 1.7 2.6 3 3 .3 0 .8-.8 1.2-.8s2.4.3 2.4 1.3c0 .8-.8 1.7-1.7 1.7-3.3 0-7.1-3.8-7.1-7.1C5.8 6.8 6.7 6 7.5 6z" fill="#fff"/></svg>
      </li>
      <li>info@flueguardianvt.example
        <svg viewBox="0 0 22 22" aria-hidden="true"><circle cx="11" cy="11" r="11" fill="#b3222a"/><rect x="5.5" y="7" width="11" height="8" fill="none" stroke="#fff" stroke-width="1.4"/><path d="M5.5 7l5.5 4.5L16.5 7" fill="none" stroke="#fff" stroke-width="1.4"/></svg>
      </li>
      <li>www.flueguardianvt.example
        <svg viewBox="0 0 22 22" aria-hidden="true"><circle cx="11" cy="11" r="11" fill="#b3222a"/><circle cx="11" cy="11" r="5.5" fill="none" stroke="#fff" stroke-width="1.3"/><ellipse cx="11" cy="11" rx="2.4" ry="5.5" fill="none" stroke="#fff" stroke-width="1.2"/><path d="M5.5 11h11" stroke="#fff" stroke-width="1.2"/></svg>
      </li>
    </ul>

    <div class="base-line"></div>
  </main>
</body>
</html>
```